Redesign a Start-Up Dating Website

Website: https://morvelique.com.
Make sure the design has an island style theme.
I would like the 7 pages of my website to have a new and professional look. I want the same colors to remain, but I want a creative look for all the pages. This is a dating website that is in the startup stage. So, I want to give my entire website a custom makeover. I want something that will stand out from the other dating sites. Something that will attract more people to want to use my services, and hopefully get new members.
Target Market(s)
Dating
Industry/Entity Type
Dating
Coding
Coded - Design and coding required
Number of Pages Required
5+ page
Font styles to use
Other font styles liked:
- Decorative, San Serif
Requirements
Must have
- The design must have the original colors and a stylish font to go along. The design must be creative, welcoming, and professional. I would like an island style theme for the website. This is a dating website so make sure that the design is tailored to that aspect.
Nice to have
- It would be nice to have a decorative font and a professional style on all the pages. Make sure the design will be mobile responsive and friendly for all the pages on the website.
Should not have
- The design should not be bland and uncreative.

```html
<!DOCTYPE html>
<html lang="en">
<head>
<meta charset="utf-8">
<title>Morvelique – Let's Find Your Perfect Match Today</title>
<link href="https://fonts.googleapis.com/css2?family=Lato:wght@300;400;700;900&display=swap" rel="stylesheet">
<style>
:root{
  --teal:#33b8a0;
  --teal-dark:#1fa58c;
  --purple:#6b3fa0;
  --purple-soft:rgba(103,58,160,.82);
  --orange:#f7941d;
  --orange-deep:#f08a1c;
  --ink:#333333;
  --muted:#8a8a8a;
  --grey-bg:#f1f1f1;
  --line:#e4e4e4;
  --white:#ffffff;
}
*{margin:0;padding:0;box-sizing:border-box}
html,body{width:1200px;height:2782px;overflow:hidden}
body{font-family:'Lato',Arial,sans-serif;color:var(--ink);background:var(--white);position:relative}
.abs{position:absolute}

/* Header */
.site-header{position:absolute;left:0;top:0;width:1200px;height:115px;background:var(--white)}
.brand{position:absolute;left:122px;top:30px;display:flex;align-items:center;gap:12px}
.brand-dot{width:62px;height:62px;border-radius:50%;background:var(--orange)}
.brand-name{font-size:46px;font-weight:700;color:var(--teal);letter-spacing:.5px}
.auth{position:absolute;top:0;display:flex}
.auth a{display:block;height:34px;line-height:34px;text-align:center;color:#fff;font-size:15px;text-decoration:none}
.btn-signup{position:absolute;left:903px;top:0;width:89px;background:var(--purple)}
.btn-login{position:absolute;left:998px;top:0;width:87px;background:var(--orange)}
.main-nav{position:absolute;top:54px;left:0;width:1200px;height:61px}
.main-nav a{position:absolute;top:0;font-size:18px;color:var(--ink);text-decoration:none}
.main-nav a.active{color:var(--teal)}
.main-nav a.active::after{content:"";position:absolute;left:-6px;right:-6px;top:56px;height:5px;background:var(--teal)}

/* Hero */
.hero{position:absolute;left:0;top:115px;width:1200px;height:610px;overflow:hidden}
.hero-photo{position:absolute;inset:0;background:radial-gradient(ellipse at 48% 30%,#c9a58a 0%,#9c7560 35%,#5e4438 70%,#3f2f29 100%)}
.hero-title{position:absolute;left:120px;top:238px;color:#fff;font-size:44px;line-height:58px;font-weight:300}
.hero-title strong{font-weight:700;display:block}
.slider-dots{position:absolute;left:552px;top:505px;display:flex;gap:9px}
.slider-dots span{width:15px;height:15px;border-radius:50%;background:#fff}
.slider-dots span:first-child{background:transparent;border:2px solid #fff}
.hero-curve{position:absolute;left:0;bottom:0}

.search-panel{position:absolute;left:736px;top:76px;width:349px;height:416px;background:var(--purple-soft);padding:34px 30px 0}
.search-panel label{display:block;color:#fff;font-size:16px;margin-bottom:6px}
.select{height:40px;background:#fff;color:#555;font-size:15px;line-height:40px;padding:0 14px;position:relative;margin-bottom:18px}
.select::after{content:"";position:absolute;right:16px;top:13px;width:8px;height:8px;border-right:1.5px solid #888;border-bottom:1.5px solid #888;transform:rotate(45deg)}
.age-row{display:flex;gap:8px}
.age-row>div{flex:1}
.btn-search{display:block;height:46px;line-height:46px;text-align:center;background:linear-gradient(#3fc6ad,var(--teal-dark));color:#fff;font-size:19px;letter-spacing:.5px;margin-top:-2px}

/* How it works */
.section-title{position:absolute;left:0;width:1200px;text-align:center;font-size:33px;font-weight:400}
.how-title{top:716px;color:var(--purple)}
.steps-path{position:absolute;left:0;top:770px}
.step{position:absolute;width:300px;text-align:center;top:775px}
.step-heart{width:160px;height:150px;margin:0 auto;position:relative}
.step-heart svg.icon{position:absolute;left:50%;top:50%;transform:translate(-50%,-62%)}
.step h3{font-size:22px;font-weight:400;color:var(--ink);margin-top:14px}
.step p{font-size:12.5px;line-height:18px;color:var(--muted);margin-top:10px;padding:0 22px}

/* Promo band */
.promo{position:absolute;left:0;top:1081px;width:1200px;height:446px;background:linear-gradient(100deg,#34b9a1 0%,#49c2ad 55%,#3bb79f 100%);text-align:center;color:#fff}
.emblem{position:absolute;width:88px;height:88px;border-radius:50%;background:#fff;box-shadow:0 2px 6px rgba(0,0,0,.15)}
.emblem::after{content:"";position:absolute;inset:12px;border-radius:50%;background:var(--orange)}
.promo h2{position:absolute;top:86px;width:100%;font-size:39px;font-weight:400}
.promo .lead{position:absolute;top:148px;width:100%;font-size:22px;line-height:28px}
.promo .lead span{display:block;font-size:19px}
.promo .body{position:absolute;top:230px;left:330px;width:540px;font-size:13.5px;line-height:24px}
.btn-outline{position:absolute;left:517px;top:325px;width:186px;height:48px;border:2px solid #fff;line-height:44px;font-size:18px;color:#fff;text-decoration:none}

/* Members */
.members{position:absolute;left:0;top:1532px;width:1200px;height:421px;background:var(--grey-bg)}
.members .section-title{top:42px;color:var(--orange)}
.member{position:absolute;top:115px;width:162px;text-align:center}
.member-photo{width:162px;height:165px}
.member h4{font-size:16px;font-weight:400;color:var(--purple);margin-top:22px}
.member p{font-size:14px;color:var(--teal);margin-top:4px}
.arrow{position:absolute;top:188px}

/* Feature cards */
.card{position:absolute;top:2022px;width:467px;height:232px;background:#fff;border-radius:8px 50px 8px 50px;box-shadow:0 6px 18px rgba(0,0,0,.13)}
.card-photo{position:absolute;left:28px;top:26px;width:180px;height:178px}
.card h3{position:absolute;left:234px;top:42px;font-size:26px;font-weight:400}
.card p{position:absolute;left:234px;top:92px;width:200px;font-size:13px;line-height:19px;color:var(--muted)}
.card a{position:absolute;left:234px;top:177px;font-size:14px;font-weight:700;color:var(--purple);text-decoration:none}

/* Footer */
.footer-rule{position:absolute;left:120px;top:2371px;width:962px;height:6px;background:var(--teal)}
.site-footer{position:absolute;left:0;top:2377px;width:1200px;height:405px;background:linear-gradient(172deg,var(--orange-deep) 0%,#d9772f 40%,#a0556a 75%,#6e4a9a 100%);color:#fff}
.footer-col{position:absolute;top:88px}
.footer-col h5{font-size:22px;font-weight:400;margin-bottom:18px}
.footer-col a,.footer-col li{display:block;list-style:none;font-size:14.5px;color:#fff;text-decoration:none;line-height:31px}
.contact li{display:flex;align-items:flex-start;gap:12px;line-height:26px}
.email-field{width:254px;height:39px;border:1px solid rgba(255,255,255,.8);display:flex;align-items:center;gap:10px;padding-left:14px;font-size:13px;margin-top:2px}
.btn-subscribe{display:block;width:143px;height:37px;margin-top:12px;background:#fbaa1a;text-align:center;line-height:37px;font-weight:700;font-size:16px;color:#fff}
.social{display:flex;gap:10px;margin-top:24px}
.social span{width:36px;height:36px;border-radius:50%;border:2px solid #fff}
.footer-divider{position:absolute;left:113px;top:330px;width:975px;height:1px;background:rgba(255,255,255,.35)}
.copyright{position:absolute;top:354px;width:100%;text-align:center;font-size:12.5px}
</style>
</head>
<body>

<header class="site-header">
  <div class="brand"><span class="brand-dot"></span><span class="brand-name">Morvelique</span></div>
  <a class="btn-signup abs" href="#" style="color:#fff;text-decoration:none;height:34px;line-height:34px;text-align:center;font-size:15px">Sign Up</a>
  <a class="btn-login abs" href="#" style="color:#fff;text-decoration:none;height:34px;line-height:34px;text-align:center;font-size:15px">Log In</a>
  <nav class="main-nav">
    <a class="active" href="#" style="left:483px">Home</a>
    <a href="#" style="left:563px">Search</a>
    <a href="#" style="left:648px">Members</a>
    <a href="#" style="left:755px">Extras</a>
    <a href="#" style="left:838px">About</a>
    <a href="#" style="left:918px">Premium</a>
    <a href="#" style="left:1021px">Contact</a>
  </nav>
</header>

<section class="hero">
  <div class="hero-photo" role="img" aria-label="Smiling couple making a heart shape with their hands"></div>
  <h1 class="hero-title">Let's Find Your<strong>Perfect Match Today</strong></h1>
  <form class="search-panel">
    <label>I am</label>
    <div class="select">Man</div>
    <label>Seeking a</label>
    <div class="select">Woman</div>
    <div class="age-row">
      <div><label>Age</label><div class="select">18</div></div>
      <div><label>To</label><div class="select">20</div></div>
    </div>
    <div class="select">Select Country</div>
    <a class="btn-search">SEARCH</a>
  </form>
  <div class="slider-dots"><span></span><span></span><span></span><span></span></div>
  <svg class="hero-curve" width="1200" height="80" viewBox="0 0 1200 80">
    <path d="M0,70 Q600,-20 1200,78 L1200,80 L0,80 Z" fill="#fff"/>
    <path d="M0,70 Q600,-20 1200,78" fill="none" stroke="#f7941d" stroke-width="8"/>
  </svg>
</section>

<h2 class="section-title how-title">How it Works</h2>
<svg class="steps-path" width="1200" height="120" viewBox="0 0 1200 120">
  <path d="M345,50 Q430,20 520,55" fill="none" stroke="#cfcfcf" stroke-width="2" stroke-dasharray="5 6"/>
  <path d="M678,70 Q760,110 850,62" fill="none" stroke="#cfcfcf" stroke-width="2" stroke-dasharray="5 6"/>
</svg>

<div class="step" style="left:115px">
  <div class="step-heart">
    <svg width="160" height="150" viewBox="0 0 160 150"><path d="M80,140 C30,105 6,78 6,46 C6,20 26,6 46,6 C62,6 74,15 80,27 C86,15 98,6 114,6 C134,6 154,20 154,46 C154,78 130,105 80,140 Z" fill="none" stroke="#e6e6e6" stroke-width="10"/></svg>
    <svg class="icon" width="50" height="54" viewBox="0 0 50 54"><circle cx="25" cy="16" r="11" fill="none" stroke="#6b3fa0" stroke-width="2.5"/><path d="M4,52 C4,38 13,31 25,31 C37,31 46,38 46,52 Z" fill="none" stroke="#6b3fa0" stroke-width="2.5"/></svg>
  </div>
  <h3>Create a Profile</h3>
  <p>Let people know all about you; the good and the quirky-show the world your true colors and find someone</p>
</div>

<div class="step" style="left:447px">
  <div class="step-heart">
    <svg width="160" height="150" viewBox="0 0 160 150"><path d="M80,140 C30,105 6,78 6,46 C6,20 26,6 46,6 C62,6 74,15 80,27 C86,15 98,6 114,6 C134,6 154,20 154,46 C154,78 130,105 80,140 Z" fill="none" stroke="#e6e6e6" stroke-width="10"/></svg>
    <svg class="icon" width="62" height="58" viewBox="0 0 62 58"><path d="M31,55 C12,42 3,32 3,19 C3,9 11,3 19,3 C25,3 29,6 31,11 C33,6 37,3 43,3 C51,3 59,9 59,19 C59,32 50,42 31,55 Z" fill="none" stroke="#f7941d" stroke-width="2.5"/><circle cx="21" cy="23" r="3" fill="#f7941d"/><circle cx="31" cy="23" r="3" fill="#f7941d"/><circle cx="41" cy="23" r="3" fill="#f7941d"/></svg>
  </div>
  <h3>Find Matches</h3>
  <p>Browse other users and feel the excitement of getting your first message and getting to know potential dates in a safe</p>
</div>

<div class="step" style="left:777px">
  <div class="step-heart">
    <svg width="160" height="150" viewBox="0 0 160 150"><path d="M80,140 C30,105 6,78 6,46 C6,20 26,6 46,6 C62,6 74,15 80,27 C86,15 98,6 114,6 C134,6 154,20 154,46 C154,78 130,105 80,140 Z" fill="none" stroke="#e6e6e6" stroke-width="10"/></svg>
    <svg class="icon" width="44" height="64" viewBox="0 0 44 64"><path d="M10,6 L16,14 L22,4 L28,14 L34,6 L34,22 C34,30 28,34 22,34 C16,34 10,30 10,22 Z" fill="none" stroke="#1fa58c" stroke-width="2.5"/><path d="M22,34 L22,62 M22,50 C14,50 8,44 6,40 C14,40 20,44 22,50 M22,46 C30,46 36,40 38,36 C30,36 24,40 22,46" fill="none" stroke="#1fa58c" stroke-width="2.5"/></svg>
  </div>
  <h3>Start Dating</h3>
  <p>Once you've found your potential soulmate, it's time to meet up and say 'Hello' to the start of your journey togethe</p>
</div>

<section class="promo">
  <div class="promo-photo abs" role="img" aria-label="Faint photo of a smiling couple under a teal tint" style="inset:0;background:radial-gradient(ellipse at 70% 50%,rgba(255,255,255,.12),rgba(255,255,255,0) 60%)"></div>
  <span class="emblem" style="left:556px;top:-30px"></span>
  <h2>Dating is Easy with Morvelique</h2>
  <p class="lead">Sign-up for a 30 days free trial<span>Enjoy all the benefits morvelique has to offer with a full membership.</span></p>
  <p class="body">commodo a mi Morbi ornare gravida elit Integer congue augue et malesuada iaculis ipsum dui aliquet felis at cursus magna nisl nec elit Praesent elementum elit at tellus nec ultricies sit amet porttitor mattis enim in massa libero interdum nec interdum vel blandit sed nulla in ullamcorper est eget</p>
  <a class="btn-outline" href="#">Get Starte Now</a>
</section>

<section class="members">
  <h2 class="section-title">Our Members</h2>
  <svg class="arrow" style="left:102px" width="20" height="34" viewBox="0 0 20 34"><path d="M17,2 L3,17 L17,32" fill="none" stroke="#bdbdbd" stroke-width="3"/></svg>
  <svg class="arrow" style="left:1055px" width="20" height="34" viewBox="0 0 20 34"><path d="M3,2 L17,17 L3,32" fill="none" stroke="#bdbdbd" stroke-width="3"/></svg>
  <div class="member" style="left:137px"><div class="member-photo" role="img" aria-label="Member portrait, smiling man outdoors" style="background:linear-gradient(160deg,#8fae6a,#6d5a45)"></div><h4>Memebr Name</h4><p>Age 20, City Area</p></div>
  <div class="member" style="left:324px"><div class="member-photo" role="img" aria-label="Member portrait, man in a dark sweater" style="background:linear-gradient(160deg,#b9d6d4,#3a3f4a)"></div><h4>Memebr Name</h4><p>Age 20, City Area</p></div>
  <div class="member" style="left:510px"><div class="member-photo" role="img" aria-label="Member portrait, blonde woman smiling" style="background:linear-gradient(160deg,#d8e4ea,#d9b48a)"></div><h4>Memebr Name</h4><p>Age 20, City Area</p></div>
  <div class="member" style="left:697px"><div class="member-photo" role="img" aria-label="Member portrait, man in a blue shirt" style="background:linear-gradient(160deg,#c5c7c9,#2f4a6e)"></div><h4>Memebr Name</h4><p>Age 20, City Area</p></div>
  <div class="member" style="left:882px"><div class="member-photo" role="img" aria-label="Member portrait, dark-haired woman" style="background:linear-gradient(160deg,#eeeeee,#7a5a48)"></div><h4>Memebr Name</h4><p>Age 20, City Area</p></div>
</section>

<article class="card" style="left:119px">
  <div class="card-photo" role="img" aria-label="Happy couple lying together holding a red heart" style="background:linear-gradient(150deg,#c44a3e,#e8c2a8 60%,#8e6a58)"></div>
  <h3 style="color:var(--orange)">Success Stories</h3>
  <p>commodo a mi Morbi ornare gravida elit Integer congue augue et malesuada iaculis ipsum dui aliquet felis at cursus</p>
  <a href="#">READ MORE &rsaquo;</a>
</article>
<article class="card" style="left:614px">
  <div class="card-photo" role="img" aria-label="Couple smiling together in warm sunlight" style="background:linear-gradient(150deg,#f1c27a,#b9855a 55%,#6d4a36)"></div>
  <h3 style="color:var(--purple)">Feature Benefits</h3>
  <p>commodo a mi Morbi ornare gravida elit Integer congue augue et malesuada iaculis ipsum dui aliquet felis at cursus</p>
  <a href="#">READ MORE &rsaquo;</a>
</article>

<div class="footer-rule"></div>
<footer class="site-footer">
  <span class="emblem" style="left:535px;top:-40px;width:86px;height:86px"></span>
  <div class="footer-col" style="left:113px">
    <h5>Quick Links</h5>
    <a href="#">Morvelique</a><a href="#">About</a><a href="#">Contact</a><a href="#">Login</a><a href="#">Testimonials</a>
  </div>
  <div class="footer-col" style="left:334px">
    <h5>Resources</h5>
    <a href="#">Members</a><a href="#">Premium</a><a href="#">Register</a><a href="#">Search</a>
  </div>
  <div class="footer-col contact" style="left:558px">
    <h5>Contact Us</h5>
    <ul>
      <li><svg width="14" height="20" viewBox="0 0 14 20" style="margin-top:4px"><path d="M7,19 C2,12 1,9 1,7 A6,6 0 0 1 13,7 C13,9 12,12 7,19 Z" fill="#fff"/><circle cx="7" cy="7" r="2.3" fill="#e08a2a"/></svg><span>48 Lagoon Crest Way #4<br>Florida 33040 FL</span></li>
      <li><svg width="18" height="18" viewBox="0 0 18 18" style="margin-top:4px"><path d="M4,1 L7,5 L5,7 C6,10 8,12 11,13 L13,11 L17,14 L15,17 C8,17 1,10 1,3 Z" fill="none" stroke="#fff" stroke-width="1.6"/></svg><span>305.555.0148</span></li>
      <li><svg width="18" height="14" viewBox="0 0 18 14" style="margin-top:6px"><rect x="1" y="1" width="16" height="12" fill="none" stroke="#fff" stroke-width="1.6"/><path d="M1,1 L9,8 L17,1" fill="none" stroke="#fff" stroke-width="1.6"/></svg><span>hello@morvelique.com</span></li>
    </ul>
  </div>
  <div class="footer-col" style="left:825px">
    <h5>Email Sign Up</h5>
    <div class="email-field"><svg width="16" height="12" viewBox="0 0 16 12"><rect x="1" y="1" width="14" height="10" fill="none" stroke="#fff" stroke-width="1.3"/><path d="M1,1 L8,7 L15,1" fill="none" stroke="#fff" stroke-width="1.3"/></svg>Email address</div>
    <span class="btn-subscribe">Subscribe</span>
    <div class="social"><span></span><span></span><span></span><span></span></div>
  </div>
  <div class="footer-divider"></div>
  <p class="copyright">© 2017 Company Name&nbsp; All right reserved&nbsp; Term of Use</p>
</footer>

</body>
</html>
```